Criação de Kit Layout de Posts para Redes Sociais (Facebook, Instagram e etc) para Outros
A empresa queria:
" empresa segmentada na área corporativa "

```html
<!DOCTYPE html>
<html lang="pt-BR">
<head>
<meta charset="UTF-8">
<title>Assista vídeos em uma velocidade incrível</title>
<link rel="stylesheet" href="https://fonts.googleapis.com/css2?family=Roboto+Condensed:ital,wght@0,700;1,700;1,800&display=swap">
<style>
  :root {
    --navy-deep: #071a3a;
    --navy: #0d2c63;
    --screen-blue: #1c5fb0;
    --screen-cyan: #3fa6e6;
    --lime: #b5d334;
    --lime-soft: #c3dc4e;
    --stripe-blue: #2f8fdc;
    --white: #ffffff;
  }
  * { margin: 0; padding: 0; box-sizing: border-box; }
  html, body {
    width: 1200px;
    height: 1200px;
    overflow: hidden;
    background: var(--navy-deep);
  }
  .post {
    position: relative;
    width: 1200px;
    height: 1200px;
    overflow: hidden;
    font-family: "Roboto Condensed", "Arial Narrow", sans-serif;
  }
  .video-wall {
    position: absolute;
    inset: 0;
    background:
      radial-gradient(ellipse at 30% 25%, var(--screen-cyan) 0%, transparent 45%),
      radial-gradient(ellipse at 80% 85%, var(--screen-blue) 0%, transparent 45%),
      linear-gradient(160deg, var(--navy) 0%, var(--screen-blue) 40%, var(--navy-deep) 100%);
  }
  .bands {
    position: absolute;
    inset: 0;
  }
  .headline {
    position: absolute;
    left: 0;
    width: 1200px;
    top: 410px;
    text-align: center;
    color: var(--white);
    font-style: italic;
    font-weight: 700;
    line-height: 1;
    text-transform: uppercase;
  }
  .headline .line {
    display: block;
    font-size: 64px;
    letter-spacing: 0.5px;
    margin-bottom: 10px;
  }
  .headline .highlight {
    display: block;
    font-size: 100px;
    font-weight: 800;
    margin-top: 6px;
  }
  .brand {
    position: absolute;
    left: 0;
    width: 1200px;
    top: 1062px;
    display: flex;
    justify-content: center;
    align-items: center;
    gap: 14px;
    color: var(--white);
  }
  .brand-name {
    font-size: 46px;
    font-weight: 700;
    font-style: normal;
    letter-spacing: 0.5px;
  }
  .brand-dot {
    width: 40px;
    height: 40px;
    border-radius: 50%;
    background: var(--white);
  }
</style>
</head>
<body>
  <main class="post">
    <div class="video-wall" role="img" aria-label="Parede de telas exibindo vídeos e canais de TV em tons de azul"></div>

    <svg class="bands" width="1200" height="1200" viewBox="0 0 1200 1200" aria-hidden="true">
      <defs>
        <linearGradient id="lime-fade" x1="0" y1="0" x2="0" y2="1">
          <stop offset="0" stop-color="var(--lime-soft)"/>
          <stop offset="1" stop-color="var(--lime)"/>
        </linearGradient>
      </defs>
      <polygon class="band-lime" points="0,470 1200,84 1200,540 0,935" fill="url(#lime-fade)" opacity="0.95"/>
      <polygon class="band-blue" points="0,935 1200,540 1200,680 0,1040" fill="var(--stripe-blue)" opacity="0.92"/>
      <g class="cursor-mark" opacity="0.35" fill="none" stroke="var(--white)" stroke-width="6">
        <circle cx="1060" cy="330" r="230"/>
        <polygon points="930,230 1150,300 1050,330 1020,430" fill="var(--white)" stroke="none" opacity="0.6"/>
      </g>
    </svg>

    <h1 class="headline">
      <span class="line">Assista videos</span>
      <span class="line">em uma velocidade</span>
      <span class="highlight">Incrível</span>
    </h1>

    <footer class="brand">
      <span class="brand-name">Linkora Telecom</span>
      <span class="brand-dot"></span>
    </footer>
  </main>
</body>
</html>
```